Veldmark Supplies Business Card

Professional business card that stand out to our potential customers. Front and back with clean modern design

Industry/Entity Type

Oil and gas

Contact Information for Business Card

Name, address, website , office phone and cell number

Requirements
Must have
• Editable files for each employee

```html
<!DOCTYPE html>
<html lang="en">
<head>
<meta charset="utf-8">
<title>Veldmark Supplies Business Card</title>
<link href="https://fonts.googleapis.com/css2?family=Montserrat:wght@400;500;800&display=swap" rel="stylesheet">
<style>
  :root {
    --stage: #474747;
    --card: #161616;
    --edge: #0aa9d0;
    --red: #ee2024;
    --blue: #06aacf;
    --ink: #ffffff;
    --muted: #9a9a9a;
    --emboss: #3a3a3a;
  }
  * { margin: 0; padding: 0; box-sizing: border-box; }
  html, body { width: 1200px; height: 801px; overflow: hidden; }
  body {
    background: var(--stage);
    font-family: "Montserrat", sans-serif;
    position: relative;
  }
  .card {
    position: absolute;
    width: 540px;
    height: 310px;
    background: var(--card);
    border-radius: 18px;
    border: 3px solid var(--edge);
    overflow: hidden;
  }
  .card--front { left: 40px; top: 245px; }
  .card--back  { left: 620px; top: 245px; }

  /* front */
  .brand {
    position: absolute;
    left: 34px;
    top: 0;
    width: 220px;
    height: 100%;
    display: flex;
    align-items: center;
    gap: 12px;
  }
  .brand__square { width: 22px; height: 22px; background: var(--red); flex: none; }
  .brand__name {
    color: var(--ink);
    font-weight: 800;
    font-size: 19px;
    letter-spacing: 1px;
    line-height: 1.15;
    text-transform: uppercase;
  }
  .divider {
    position: absolute;
    left: 262px;
    top: 40px;
    width: 2px;
    height: 228px;
    background: var(--red);
  }
  .details {
    position: absolute;
    left: 290px;
    top: 38px;
    color: var(--ink);
  }
  .person__name {
    font-weight: 800;
    font-size: 25px;
    letter-spacing: 1px;
    text-transform: uppercase;
    line-height: 1;
  }
  .person__first { color: var(--red); }
  .person__last  { color: var(--blue); }
  .person__role  { font-size: 13px; margin-top: 8px; }
  .address { font-size: 12.5px; line-height: 1.55; margin-top: 16px; }
  .contacts { list-style: none; margin-top: 14px; font-size: 12.5px; line-height: 1.75; }
  .contacts li { display: flex; align-items: center; gap: 8px; }
  .contacts svg { width: 13px; height: 13px; fill: var(--red); flex: none; }

  /* back */
  .back-brand {
    position: absolute;
    inset: 0;
    display: flex;
    align-items: center;
    justify-content: center;
    gap: 14px;
  }
  .back-brand__square { width: 30px; height: 30px; background: var(--emboss); }
  .back-brand__name {
    color: var(--emboss);
    font-weight: 800;
    font-size: 28px;
    letter-spacing: 2px;
    text-transform: uppercase;
  }
</style>
</head>
<body>

<section class="card card--front" aria-label="Card front">
  <div class="brand">
    <span class="brand__square"></span>
    <span class="brand__name">Veldmark<br>Supplies</span>
  </div>
  <div class="divider"></div>
  <div class="details">
    <h1 class="person__name"><span class="person__first">Daniel</span> <span class="person__last">Reyes</span></h1>
    <p class="person__role">Managing Director</p>
    <p class="address">412 N.Ridgeline Suite 5<br>Midland, Tx 79701</p>
    <ul class="contacts">
      <li><svg viewBox="0 0 16 16" aria-hidden="true"><path d="M3 1l3 3-2 2c1 2 3 4 5 5l2-2 3 3-2 3C6 15 1 10 1 3z"/></svg>(555)214-0387</li>
      <li><svg viewBox="0 0 16 16" aria-hidden="true"><path d="M4 0h8a1 1 0 011 1v14a1 1 0 01-1 1H4a1 1 0 01-1-1V1a1 1 0 011-1zm1 2v10h6V2zm3 11a1 1 0 100 2 1 1 0 000-2z"/></svg>555 832 719</li>
      <li><svg viewBox="0 0 16 16" aria-hidden="true"><path d="M0 3h16v10H0zm1.5 1.2L8 9l6.5-4.8V4h-13z"/></svg>sales@veldmarksupplies.com</li>
      <li><svg viewBox="0 0 16 16" aria-hidden="true"><path d="M8 0a8 8 0 110 16A8 8 0 018 0zm0 1.5a6.5 6.5 0 100 13 6.5 6.5 0 000-13zM2 7.2h12v1.6H2zM7.2 2h1.6v12H7.2z"/></svg>www.veldmarksupplies.com</li>
    </ul>
  </div>
</section>

<section class="card card--back" aria-label="Card back">
  <div class="back-brand">
    <span class="back-brand__square"></span>
    <span class="back-brand__name">Veldmark Supplies</span>
  </div>
</section>

</body>
</html>
```